Foot doctor needs feet friendly business cards.

Business cards for Podiatrist. Needs to look professional and modern. Back side put an appointment card, and try to put a little basic street map somewhere on card along with all of our contact info below:

Marcus Dovan, DPM, Inc.
Diplomate, National Council of Lower Limb Medicine
Call: 1.877.Toes.482
1.555.283.9146
Fax: 1.555.671.3820
Email: info@DrDovanclinic.example
Web: www.DrDovanclinic.example
2847 W. Harbor Ln. Suite 204
Costa Mesa, CA 90000

```html
<!DOCTYPE html>
<html lang="en">
<head>
<meta charset="utf-8">
<title>Marcus Dovan, DPM – Business Card</title>
<link rel="stylesheet" href="https://fonts.googleapis.com/css2?family=Lato:wght@400;700;900&display=swap">
<style>
  :root {
    --card-white: #ffffff;
    --accent-orange: #ea5a1f;
    --caduceus-blue: #2a9fd8;
    --foot-white: #ffffff;
    --edge-dark: #333333;
    --ink: #2b2b2b;
    --ink-soft: #555555;
    --rule: #333333;
  }
  * { margin: 0; padding: 0; box-sizing: border-box; }
  html, body {
    width: 1200px; height: 720px; overflow: hidden;
    background: var(--card-white);
    font-family: "Lato", sans-serif;
    color: var(--ink);
  }
  .card { position: relative; width: 1200px; height: 720px; background: var(--card-white); }
  .brand-panel {
    position: absolute; left: 80px; top: 0; width: 400px; height: 720px;
    background: var(--accent-orange);
  }
  .caduceus-emblem {
    position: absolute; left: 53px; top: 59px; width: 299px; height: 282px;
    background: var(--caduceus-blue); border-radius: 6px;
  }
  .footprints {
    position: absolute; left: 72px; top: 413px; width: 251px; height: 232px;
    background: var(--foot-white); border-radius: 6px;
  }
  .edge-band {
    position: absolute; right: 0; top: 0; width: 80px; height: 720px;
    background: var(--edge-dark);
  }
  .name {
    position: absolute; left: 526px; top: 62px;
    font-size: 37px; line-height: 1; letter-spacing: -0.5px; color: var(--ink);
  }
  .name .first { font-weight: 900; }
  .name .last { font-weight: 400; }
  .credentials {
    position: absolute; left: 526px; top: 105px;
    font-size: 25px; font-weight: 400; line-height: 1; color: var(--ink-soft);
  }
  .board {
    position: absolute; left: 493px; top: 158px;
    font-size: 19px; font-weight: 700; line-height: 1; color: var(--ink-soft);
  }
  .rule {
    position: absolute; left: 523px; width: 554px; height: 2px; background: var(--rule);
  }
  .rule.top { top: 228px; }
  .rule.bottom { top: 340px; }
  .services {
    position: absolute; left: 517px; top: 246px;
    font-size: 31px; font-weight: 900; line-height: 41px; color: var(--ink);
    letter-spacing: -0.3px;
  }
  .contact { position: absolute; left: 526px; top: 0; }
  .contact-row { position: absolute; left: 0; display: flex; align-items: flex-start; }
  .contact-icon { width: 26px; height: 26px; fill: var(--ink); }
  .contact-text {
    position: absolute; left: 70px; top: -2px; white-space: nowrap;
    font-size: 22px; font-weight: 700; line-height: 31px; color: var(--ink);
  }
  .row-phone { top: 380px; }
  .row-fax { top: 465px; }
  .row-email { top: 512px; }
  .row-web { top: 548px; }
  .row-address { top: 592px; }
</style>
</head>
<body>
<main class="card">
  <section class="brand-panel">
    <div class="caduceus-emblem" role="img" aria-label="Blue caduceus medical emblem with wings and serpents"></div>
    <div class="footprints" role="img" aria-label="Pair of white bare footprints"></div>
  </section>

  <div class="edge-band"></div>

  <h1 class="name"><span class="first">MARCUS</span> <span class="last">DOVAN</span></h1>
  <p class="credentials">DPM, Inc.</p>
  <p class="board">DIPLOMAT, NATIONAL COUNCIL OF LOWER LIMB MEDICINE</p>

  <div class="rule top"></div>
  <p class="services">NAIL FUNGUS LASER TREATMENTS<br>HEEL PAIN RELIEF SPECIALIST</p>
  <div class="rule bottom"></div>

  <div class="contact">
    <div class="contact-row row-phone">
      <svg class="contact-icon" viewBox="0 0 26 26" aria-hidden="true">
        <path d="M3 8c0-3 4-5 10-5s10 2 10 5v2h-5V8c-1-1-9-1-10 0v2H3z"/>
        <path d="M6 12h14l3 10H3z"/>
      </svg>
      <span class="contact-text">1 877 8637 482<br>1.555.283.9146</span>
    </div>
    <div class="contact-row row-fax">
      <svg class="contact-icon" viewBox="0 0 26 26" aria-hidden="true">
        <rect x="7" y="3" width="12" height="6"/>
        <path d="M3 10h20v9h-4v-4H7v4H3z"/>
        <rect x="8" y="16" width="10" height="7"/>
      </svg>
      <span class="contact-text">1.555.671.3820</span>
    </div>
    <div class="contact-row row-email">
      <svg class="contact-icon" viewBox="0 0 26 26" aria-hidden="true">
        <path d="M2 5h22v16H2z M4.5 7l8.5 7 8.5-7v-0H4.5z M4 19h18V9.5l-9 7-9-7z" fill-rule="evenodd"/>
      </svg>
      <span class="contact-text">info@DrDovanclinic.example</span>
    </div>
    <div class="contact-row row-web">
      <svg class="contact-icon" viewBox="0 0 26 26" aria-hidden="true">
        <path d="M2 3h22v15H2z M4 5v11h18V5z" fill-rule="evenodd"/>
        <rect x="11" y="18" width="4" height="4"/>
        <rect x="7" y="22" width="12" height="2"/>
      </svg>
      <span class="contact-text">www.DrDovanclinic.example</span>
    </div>
    <div class="contact-row row-address">
      <svg class="contact-icon" viewBox="0 0 26 26" aria-hidden="true">
        <path d="M13 2L1 13h3v11h7v-7h4v7h7V13h3z"/>
      </svg>
      <span class="contact-text">2847 W. Harbor Ln. Suite 204<br>Costa Mesa, CA 90000</span>
    </div>
  </div>
</main>
</body>
</html>
```